Water Delivery Service Website

We are working with BrivoNessé. They are a water delivery company and in need of a new website design.
Some sites to use for inspiration:
https://www.pelmoriston.example/home
https://www.quintalbrook.example/en/home3
https://www.drevik.example
https://www.tormaxel.example
Thank you for taking the time to consider designing a website for us. We are web developers based in Stockton, CA, USA. Most of our projects go through the same process. Understanding this process may help you win a project with us. We custom-code all of our websites in-house. We don’t have any requirements as to what tools you use for your design, but we prefer Figma files. For any design that we label as four-stars, we send it to the client for review. The client picks the final design they want us to use. Once we complete this process, we will continue to show additional clients all the four-star sites and purchase them later. Your designs will have multiple chances to sell. For better chances of success, we ask that you follow these guidelines.
IMAGES:
If you use any images or icons in the design, we ask that you have a link to the asset so we can purchase the image/icon. Most of the designs we submit do not have the customer’s images on them unless they have some great images. Be creative; show us the feeling you are trying to portray with your image choices. Use any royalty-free site you choose. We subscribe to Vantrel and mainly use their images, but we can purchase images outside of Vantrel.
PLEASE NOTE: we will not submit designs to clients with watermarks on the images.
FONTS:
We ask that you identify the fonts used in the design. This can be done in a message if you want. We typically use Google Fonts and Vantrel Fonts.
CONTENT:
We're always open to different content and ideas. We often submit designs with stock images so the client can see our vision. We typically take pictures after the website launch to use their images with our vision. Lorem Ipsum is fine for paragraphs, but we ask that you write the headers in correct English. We want to be able to show the vision and identify the sections of the website.
INSPIRATION:
We typically add a couple of links in the brief of websites we like to help you get started in your design.
REVISIONS:
We do not often ask for revisions of the designs unless we see something in the design that may not appeal to the client. If there are slight changes that we want to make, we do that in the development process.
FEEDBACK:
We rarely give feedback on designs during the design process. We are working on many website projects and do not have the time to provide feedback. We usually respond if your request is well thought out and asks specific questions, but a note asking “feedback, please” usually goes unanswered.

```html
<!DOCTYPE html>
<html lang="en">
<head>
<meta charset="utf-8">
<title>BrivoNessé — Water Delivery</title>
<link rel="stylesheet" href="https://fonts.googleapis.com/css2?family=Mulish:wght@400;500;600;700;800;900&display=swap">
<style>
:root{
  --navy:#1c1a5b;
  --blue:#1e9be0;
  --blue-dark:#1580c4;
  --ink:#2b2b3a;
  --muted:#c9cbe0;
  --grey-bg:#ebebeb;
  --card-img:#dcdcdc;
  --white:#ffffff;
}
*{margin:0;padding:0;box-sizing:border-box}
html,body{width:1200px;height:4087px;overflow:hidden}
body{font-family:"Mulish",sans-serif;color:var(--ink);background:var(--white);position:relative}
.abs{position:absolute}
.btn{position:absolute;display:flex;align-items:center;justify-content:center;background:var(--blue);color:var(--white);font-weight:800;font-size:12px;letter-spacing:.3px;text-transform:uppercase;border-radius:30px;box-shadow:0 3px 8px rgba(30,155,224,.35)}
.h2{font-weight:900;color:var(--navy);line-height:1.22}
.rule{position:absolute;height:3px;width:36px;background:var(--blue)}
.rule.light{background:var(--white)}

/* hero */
.hero{top:0;left:0;width:1200px;height:665px;background:linear-gradient(90deg,#e8ebe8 0%,#dfe3df 30%,#b9bfb8 55%,#8f978d 100%)}
.hero-photo{top:0;left:0;width:1200px;height:665px;background:radial-gradient(ellipse 260px 330px at 790px 360px,#6b5347 0%,#8a7466 35%,rgba(160,160,150,0) 75%),radial-gradient(ellipse 280px 300px at 360px 300px,rgba(110,140,100,.35),rgba(0,0,0,0) 70%)}
.logo{display:flex;align-items:center;gap:10px}
.logo-dot{width:22px;height:22px;border-radius:50%;background:var(--blue)}
.logo-name{font-weight:800;color:var(--blue);font-size:30px;letter-spacing:-.3px}
.topbar{top:24px;left:828px;display:flex;align-items:center;gap:24px;font-size:12px;color:var(--white)}
.nav{top:58px;left:527px;display:flex;gap:10px;font-size:12px;font-weight:700;color:var(--white)}
.nav a{padding:7px 12px;border-radius:20px;color:inherit;text-decoration:none}
.nav a.active{background:var(--blue)}
.hero h1{position:absolute;left:148px;top:183px;font-size:52px;font-weight:900;color:var(--navy);line-height:57px}
.hero p{position:absolute;left:148px;top:430px;width:360px;font-size:23px;line-height:29px;color:var(--navy)}
.dots{top:617px;left:563px;display:flex;gap:11px}
.dots span{width:10px;height:10px;border-radius:50%;background:rgba(255,255,255,.75)}
.dots span:first-child{background:var(--navy)}

/* waters */
.waters{top:665px;left:0;width:1200px;height:563px;background:var(--grey-bg)}
.card{position:absolute;top:150px;width:279px;height:365px;background:var(--white);border-radius:10px;overflow:hidden}
.card-img{height:210px;background:var(--card-img)}
.card h3{margin:28px 0 0 31px;font-size:21px;font-weight:900;color:var(--navy)}
.card p{margin:12px 30px 0 31px;font-size:11.5px;line-height:18px;color:var(--ink)}
.card .more{margin:14px 0 0 31px;font-size:11px;font-weight:800;color:var(--blue);text-decoration:underline}

/* convenience */
.conv{top:1228px;left:0;width:1200px;height:629px}
.list{list-style:none;position:absolute;left:649px;top:340px;font-size:13.5px}
.list li{display:flex;align-items:center;gap:16px;height:27px}
.list li::before{content:"";width:10px;height:10px;border-radius:50%;background:var(--blue)}
.body-text{position:absolute;font-size:13.5px;line-height:19px;color:var(--ink)}

/* guarantee */
.guar{top:1857px;left:0;width:1200px;height:465px;background:var(--navy);color:var(--white)}
.feat{position:absolute;top:185px;width:190px;text-align:center}
.feat svg{display:block;margin:0 auto}
.feat h3{margin-top:32px;font-size:22px;font-weight:600;line-height:27px}
.feat p{margin-top:14px;font-size:11.5px;line-height:16px;color:var(--muted)}

/* plans */
.plans{top:2322px;left:0;width:1200px;height:578px}

/* delivered */
.deliv{top:2900px;left:0;width:1200px;height:505px;background:linear-gradient(90deg,#cfc9c0 0%,#8d8a85 40%,#474a4f 62%,#3a3d42 100%)}

/* consult */
.consult{top:3405px;left:0;width:1200px;height:335px;background:linear-gradient(110deg,#f6f6f7 0%,#e9eaec 40%,#f4f4f5 60%,#e6e7ea 100%);text-align:center}

/* footer */
.footer{top:3740px;left:0;width:1200px;height:347px;background:var(--navy);color:var(--white)}
.foot-h{position:absolute;font-size:13px;font-weight:800;letter-spacing:.3px}
.foot-row{position:absolute;display:flex;gap:18px;font-size:13px;line-height:18px}
.foot-menu{position:absolute;left:780px;top:90px;list-style:none;font-size:13px;line-height:22.5px}
.social{position:absolute;left:895px;top:80px;display:flex;gap:6px}
.social span{width:25px;height:25px;border-radius:50%;border:2px solid var(--white)}
</style>
</head>
<body>

<!-- Hero -->
<section class="abs hero">
  <div class="abs hero-photo" role="img" aria-label="Photo of a woman drinking a glass of water in a bright room with green plants"></div>
  <div class="abs logo" style="left:150px;top:48px"><span class="logo-dot"></span><span class="logo-name">BrivoNessé</span></div>
  <div class="abs topbar">
    <span style="display:flex;align-items:center;gap:8px">
      <svg width="12" height="12" viewBox="0 0 24 24" fill="#fff"><path d="M6.6 10.8a15 15 0 0 0 6.6 6.6l2.2-2.2a1 1 0 0 1 1-.25 11.4 11.4 0 0 0 3.6.57 1 1 0 0 1 1 1V20a1 1 0 0 1-1 1A17 17 0 0 1 3 4a1 1 0 0 1 1-1h3.5a1 1 0 0 1 1 1c0 1.25.2 2.45.57 3.57a1 1 0 0 1-.25 1z"/></svg>
      1- 555 0142 2290</span>
    <svg width="17" height="17" viewBox="0 0 24 24" fill="none" stroke="#fff" stroke-width="2"><circle cx="10" cy="10" r="7"/><path d="M15 15l6 6"/></svg>
    <svg width="20" height="20" viewBox="0 0 24 24" fill="none" stroke="#fff" stroke-width="2"><rect x="4" y="8" width="16" height="13" rx="1"/><path d="M8 8V6a4 4 0 0 1 8 0v2"/><circle cx="20" cy="4" r="4" fill="#1e9be0" stroke="none"/></svg>
  </div>
  <nav class="abs nav">
    <a class="active" href="#">HOME</a><a href="#">ABOUT US</a><a href="#">WATER</a><a href="#">SHOP</a><a href="#">SERVICES</a><a href="#">CONTACT US</a>
  </nav>
  <h1>Pure &amp;<br>Fresh Water,<br>Delivered<br>to You</h1>
  <p>Reliable and convenient water delivery for homes and businesses.</p>
  <a class="btn" style="left:148px;top:540px;width:217px;height:47px">Start Water Delivery</a>
  <div class="abs dots"><span></span><span></span><span></span><span></span></div>
</section>

<!-- Our Waters -->
<section class="abs waters">
  <h2 class="h2 abs" style="top:40px;width:1200px;text-align:center;font-size:33px">Our Waters</h2>
  <div class="rule" style="left:583px;top:104px"></div>
  <article class="card" style="left:151px">
    <div class="card-img" role="img" aria-label="Three large blue water jugs"></div>
    <h3>Big Bottles</h3>
    <p>Lorem Ipsum is simply dummy text of the printing and typesetting.</p>
    <div class="more">READ MORE ›</div>
  </article>
  <article class="card" style="left:461px">
    <div class="card-img" role="img" aria-label="Three plastic water bottles"></div>
    <h3>Water Bottles</h3>
    <p>Lorem Ipsum is simply dummy text of the printing and typesetting.</p>
    <div class="more">READ MORE ›</div>
  </article>
  <article class="card" style="left:771px">
    <div class="card-img" role="img" aria-label="Water softening filter cartridges"></div>
    <h3>Water Softening</h3>
    <p>Lorem Ipsum is simply dummy text of the printing and typesetting.</p>
    <div class="more">READ MORE ›</div>
  </article>
</section>

<!-- Convenience -->
<section class="abs conv">
  <div class="abs" role="img" aria-label="Delivery worker with clipboard and customer beside a large water jug in a kitchen" style="left:153px;top:64px;width:436px;height:502px;border-radius:8px;background:linear-gradient(135deg,#e9ecef 0%,#cfd6dd 50%,#8fb3d4 100%)"></div>
  <h2 class="h2 abs" style="left:646px;top:50px;font-size:37px;line-height:45px">Convenience at Your<br>Doorstep : Hassle-Free<br>Water Supply</h2>
  <div class="rule" style="left:649px;top:205px"></div>
  <p class="body-text" style="left:649px;top:237px;width:392px">Lorem ipsum dolor sit amet, consectetur adipiscing elit, sed do eiusmod tempor incididunt ut labore et dolore magna aliqua. Ut enim ad minim veniam, quis nostrud exercitation ullamco laboris</p>
  <ul class="list">
    <li>Easy Online Ordering</li>
    <li>Flexible Delivery Schedules</li>
    <li>No Heavy Lifting</li>
    <li>Reliable &amp; Timely Service</li>
    <li>Subscription &amp; On-Demand Options</li>
    <li>High-Quality &amp; Purified Water</li>
  </ul>
  <a class="btn" style="left:653px;top:519px;width:139px;height:46px">Read More</a>
</section>

<!-- Better Water, Guaranteed -->
<section class="abs guar">
  <h2 class="abs" style="top:60px;width:1200px;text-align:center;font-size:36px;font-weight:800">Better Water, Guaranteed</h2>
  <div class="rule light" style="left:567px;top:128px;width:66px;height:2px"></div>
  <div class="feat" style="left:148px">
    <svg width="70" height="70" viewBox="0 0 70 70" fill="none" stroke="#1e9be0" stroke-width="2.5" stroke-linecap="round"><path d="M35 10c-7 10-11 16-11 22a11 11 0 0 0 22 0c0-6-4-12-11-22z"/><path d="M8 30c0 16 10 26 22 32M62 30c0 16-10 26-22 32"/></svg>
    <h3>Unmatched<br>Care</h3>
    <p>Lorem ipsum dolor sit amet, consectetur adipiscing elit, sed do eiusmod tempo.</p>
  </div>
  <div class="feat" style="left:380px">
    <svg width="70" height="70" viewBox="0 0 70 70" fill="none" stroke="#1e9be0" stroke-width="2.5" stroke-linecap="round"><path d="M24 64V50c-6-4-10-10-10-18a22 22 0 0 1 44 0l5 9h-5v9a5 5 0 0 1-5 5h-6v9"/><circle cx="36" cy="30" r="8"/></svg>
    <h3>Peace of<br>Mind</h3>
    <p>Lorem ipsum dolor sit amet, consectetur adipiscing elit, sed do eiusmod tempo.</p>
  </div>
  <div class="feat" style="left:621px">
    <svg width="70" height="70" viewBox="0 0 70 70" fill="none" stroke="#1e9be0" stroke-width="2.5" stroke-linecap="round"><circle cx="35" cy="38" r="18"/><circle cx="35" cy="38" r="7"/><path d="M35 4v8M14 12l5 6M56 12l-5 6M4 30h8M58 30h8"/></svg>
    <h3>Sustainable<br>Solutions</h3>
    <p>Lorem ipsum dolor sit amet, consectetur adipiscing elit, sed do eiusmod tempo.</p>
  </div>
  <div class="feat" style="left:869px">
    <svg width="70" height="70" viewBox="0 0 70 70" fill="none" stroke="#1e9be0" stroke-width="2.5"><circle cx="35" cy="35" r="27"/><ellipse cx="35" cy="35" rx="12" ry="27"/><path d="M8 35h54M13 21h44M13 49h44"/></svg>
    <h3>For Anyone,<br>Anywhere</h3>
    <p>Lorem ipsum dolor sit amet, consectetur adipiscing elit, sed do eiusmod tempo.</p>
  </div>
</section>

<!-- Plans -->
<section class="abs plans">
  <h2 class="h2 abs" style="left:148px;top:68px;font-size:37px;line-height:45px">Affordable and<br>Flexible Water Plans<br>for Everyone</h2>
  <div class="rule" style="left:149px;top:223px"></div>
  <p class="body-text" style="left:149px;top:260px;width:362px;line-height:21px">Lorem ipsum dolor sit amet, consectetur adipiscing elit, sed do eiusmod tempor incididunt ut labore et dolore magna aliqua. Ut enim ad minim veniam, quis nostrud exercitation ullamco laboris magni dolores eos qui ratione voluptatem sequi nesciunt. Neque porro quisquam est, qui dolorem ipsum quia dolor sit amet, consectetur, adipisci velit, sed quia non numquam eius modi tempora incidunt ut labor.</p>
  <a class="btn" style="left:149px;top:456px;width:139px;height:46px">Read More</a>
  <div class="abs" role="img" aria-label="Hand pressing a manual pump on a water jug, filling a glass" style="left:583px;top:65px;width:463px;height:440px;border-radius:8px;background:linear-gradient(135deg,#eef0f1 0%,#dfe4e8 45%,#9cc3e4 75%,#5b96cf 100%)"></div>
</section>

<!-- Get High-Quality Water -->
<section class="abs deliv" role="img" aria-label="Large water jug with electric pump on a kitchen counter">
  <h2 class="abs" style="left:668px;top:62px;font-size:37px;line-height:45px;font-weight:900;color:#fff">Get High-Quality<br>Water Delivered</h2>
  <div class="rule light" style="left:675px;top:184px;width:38px;height:2px"></div>
  <p class="body-text" style="left:674px;top:218px;width:350px;font-size:14.5px;line-height:20px;color:#fff">Lorem ipsum dolor sit amet, consectetur adipiscing elit, sed do eiusmod tempor incididunt ut labore et dolore magna aliqua. Ut enim ad minim veniam, quis nostrud exercitation ullamco laboris magni dolores eos qui ratione voluptatem sequi nesciunt. Neque porro quisquam est, qui dolorem</p>
  <a class="btn" style="left:676px;top:382px;width:190px;height:46px">Get Water Delivery</a>
</section>

<!-- Consultation -->
<section class="abs consult">
  <h2 class="h2 abs" style="top:72px;width:1200px;font-size:33px">Schedule a Free Consultation</h2>
  <p class="abs" style="left:330px;top:135px;width:540px;font-size:15.5px;line-height:25px;color:#4a4a58">Lorem ipsum dolor sit amet, consectetur adipiscing elit, sed do eiusmod tempor incididunt ut labore et dolore magna aliqua. Ut enim ad minim veniam, quis nostrud exercitation ullamco laboris</p>
  <a class="btn" style="left:527px;top:225px;width:146px;height:45px">Get Started</a>
</section>

<!-- Footer -->
<footer class="abs footer">
  <div class="abs logo" style="left:152px;top:105px"><span class="logo-dot" style="width:30px;height:30px"></span><span class="logo-name" style="font-size:44px">BrivoNessé</span></div>
  <div class="foot-h" style="left:511px;top:52px">CONTACT US</div>
  <div class="foot-row" style="left:520px;top:92px">
    <svg width="12" height="16" viewBox="0 0 24 32" fill="#fff"><path d="M12 0a12 12 0 0 0-12 12c0 9 12 20 12 20s12-11 12-20A12 12 0 0 0 12 0zm0 17a5 5 0 1 1 0-10 5 5 0 0 1 0 10z"/></svg>
    <span>4180 Marlow Crest Rd<br>Fenwick, WI 53990</span>
  </div>
  <div class="foot-row" style="left:520px;top:148px">
    <svg width="13" height="13" viewBox="0 0 24 24" fill="#fff"><path d="M6.6 10.8a15 15 0 0 0 6.6 6.6l2.2-2.2a1 1 0 0 1 1-.25 11.4 11.4 0 0 0 3.6.57 1 1 0 0 1 1 1V20a1 1 0 0 1-1 1A17 17 0 0 1 3 4a1 1 0 0 1 1-1h3.5a1 1 0 0 1 1 1c0 1.25.2 2.45.57 3.57a1 1 0 0 1-.25 1z"/></svg>
    <span>+1 555 014 2290</span>
  </div>
  <div class="foot-row" style="left:520px;top:187px">
    <svg width="14" height="12" viewBox="0 0 24 20" fill="#fff"><path d="M0 2a2 2 0 0 1 2-2h20a2 2 0 0 1 2 2v.5L12 10 0 2.5zM0 5l12 7.5L24 5v13a2 2 0 0 1-2 2H2a2 2 0 0 1-2-2z"/></svg>
    <span>info@BrivoNessé.com</span>
  </div>
  <div class="foot-h" style="left:780px;top:57px">MENU</div>
  <ul class="foot-menu">
    <li>Home</li><li>About us</li><li>Water</li><li>Shop</li><li>Services</li><li>Contact us</li>
  </ul>
  <div class="foot-h" style="left:895px;top:52px">FOLLOW US</div>
  <div class="social"><span></span><span></span><span></span><span></span><span></span></div>
  <div class="abs" style="left:152px;top:252px;width:898px;height:3px;background:var(--blue)"></div>
  <div class="abs" style="top:305px;width:1200px;text-align:center;font-size:12px;color:var(--muted)">Copyright © 2025 All Rights Reserved</div>
</footer>

</body>
</html>
```